Request for Business Card Design

Hi. My name is Marlene, I am looking for a new business card design for my company, Quarrow Signal Instruments, LLC. I really like the design you did for Tarsel Venture and was hoping you could do something similar using our full logo and our mark. I am also open to any raised texture design using our mark. I have attached our full logo, which would need to be somewhere on the card, as well as the mark in both outline and full form, as well as our brand colors / guide. The card does not have to be white, as long as our logo and mark appear. I actually like darker colored business cards more, but am open to all options. If you are interested in working with me, please let me know. We would also take the business card design into letterhead design if you can do that.

```html
<!DOCTYPE html>
<html lang="en">
<head>
<meta charset="utf-8">
<title>Quarrow Signal Instruments – Business Card</title>
<link href="https://fonts.googleapis.com/css2?family=Montserrat:wght@400;500;600;700&display=swap" rel="stylesheet">
<style>
  :root {
    --backdrop: #4a423d;
    --card: #1b1b1c;
    --card-deep: #121213;
    --accent: #1a9ac9;
    --ink: #f2f2f2;
    --ink-soft: #d6d6d6;
  }
  * { margin: 0; padding: 0; box-sizing: border-box; }
  html, body {
    width: 1200px; height: 786px; overflow: hidden;
    background: var(--backdrop);
    font-family: "Montserrat", sans-serif;
  }
  .stage {
    width: 1200px; height: 786px;
    display: flex; align-items: center; justify-content: center; gap: 40px;
  }
  .card {
    width: 540px; height: 309px;
    background: var(--card);
    position: relative;
    box-shadow: 0 12px 30px rgba(0,0,0,.45);
    overflow: hidden;
  }
  /* Brand lockup */
  .brand {
    position: absolute;
    display: flex; align-items: center; gap: 12px;
  }
  .brand-dot {
    width: 30px; height: 30px; border-radius: 50%;
    background: var(--accent);
    flex: none;
  }
  .brand-name {
    color: var(--ink);
    font-weight: 600;
    font-size: 15px;
    line-height: 1.2;
    letter-spacing: .06em;
    text-transform: uppercase;
  }
  /* Front */
  .card-front .brand { left: 40px; top: 130px; }
  .divider {
    position: absolute; left: 268px; top: 92px;
    width: 2px; height: 128px; background: var(--accent);
  }
  .contact {
    position: absolute; left: 290px; top: 86px;
    color: var(--ink-soft);
  }
  .contact-name {
    color: var(--accent); font-weight: 700; font-size: 20px; line-height: 1.1;
  }
  .contact-role { font-size: 11px; margin: 2px 0 8px; }
  .contact-list { list-style: none; font-size: 11px; line-height: 1.55; }
  .contact-list li { display: flex; align-items: center; gap: 7px; }
  .contact-list svg { width: 9px; height: 9px; fill: var(--accent); flex: none; }
  .contact-address { font-size: 11px; line-height: 1.4; margin-top: 8px; }
  /* Back */
  .raised-mark {
    position: absolute; left: 0; top: 0; width: 300px; height: 309px;
    background: radial-gradient(circle at 45% 50%, #3a3a3c 0%, #202022 45%, var(--card-deep) 75%);
  }
  .card-back .brand { right: 30px; top: 130px; }
</style>
</head>
<body>
<main class="stage">
  <section class="card card-front" aria-label="Business card front">
    <div class="brand">
      <span class="brand-dot"></span>
      <span class="brand-name">Quarrow Signal<br>Instruments</span>
    </div>
    <span class="divider"></span>
    <div class="contact">
      <p class="contact-name">Marlene Ashby</p>
      <p class="contact-role">Owner</p>
      <ul class="contact-list">
        <li><svg viewBox="0 0 10 10"><path d="M2 1l2 2-1 1.3a6 6 0 0 0 2.7 2.7L7 6l2 2-1.3 1.4C4 9 1 6 .6 2.3z"/></svg>+001 303 555 0142</li>
        <li><svg viewBox="0 0 10 10"><path d="M0 2h10v6H0z M0 2l5 3.5L10 2" /></svg>info@quarrowsignal.com</li>
        <li><svg viewBox="0 0 10 10"><circle cx="5" cy="5" r="4.5"/></svg>www.quarrowsignal.com</li>
      </ul>
      <p class="contact-address">1180 Ridgeline Parkway<br>Fenmore, CO 80599</p>
    </div>
  </section>
  <section class="card card-back" aria-label="Business card back">
    <div class="raised-mark" role="img" aria-label="Large raised brand mark in gloss black"></div>
    <div class="brand">
      <span class="brand-dot"></span>
      <span class="brand-name">Quarrow Signal<br>Instruments</span>
    </div>
  </section>
</main>
</body>
</html>
```